Präsentationsvorlagen für Strahlenschutzkurse
Zielgruppe
Wir bieten Strahlenschutzkurse in der Medizin an. Zielgruppe: Ärztinnen und Ärzte
Stichworte: Erwachsenenbildung, wissenschaftliche Inhalte
Aufgabenstellung
Wir benötigen eine Power-Point Präsentationsvorlage für unsere Kurse.
Auf allen Folien:
*Integration von unserem Logo
*Übernahme unseres bestehenden Farbkonzepts
*Feld für Überschrift
*kleines Textfeld für die Angabe der jeweiligen Quelle
Wir benötigen:
eine Folie nur mit Textfeld (z.B. Aufzählung, kurzer Text)
eine Folie Text mit Bild
eine Folie Bild bzw. Video
eine Folie mit einem wichtigen Lehrinhalt (wichtiger Text) - besondere Vorhebung erwünscht
eine Folie für Anfang bzw. Ende
HEX-CODE:
#4f93fe
#eea62f
#ffffff

```html
<!DOCTYPE html>
<html lang="de">
<head>
<meta charset="utf-8">
<title>Präsentationsvorlage Strahlenschutzkurse</title>
<link rel="stylesheet" href="https://fonts.googleapis.com/css2?family=Lato:wght@400;700&display=swap">
<style>
  :root{
    --page:#ececec;
    --navy:#47618f;
    --headline:#3e5c8a;
    --band:#a5b9da;
    --band-soft:#b3c5e2;
    --accent:#5b86c9;
    --white:#ffffff;
    --body:#2f3a4a;
    --photo-a:#d9dadd;
    --photo-b:#f4f4f5;
  }
  *{box-sizing:border-box;margin:0;padding:0}
  html,body{width:750px;height:1200px;overflow:hidden;background:var(--page);font-family:"Lato",sans-serif}
  .deck{position:absolute;left:51px;top:310px;display:grid;grid-template-columns:315px 315px;gap:20px 18px}
  .slide{position:relative;width:315px;height:177px;background:var(--white);overflow:hidden}
  .slide--dark{background:var(--navy)}
  .backdrop{position:absolute;inset:0;background:linear-gradient(160deg,#56709c 0%,#44608e 55%,#3b557f 100%)}
  .brand{position:absolute;display:flex;align-items:center;gap:4px;color:var(--white);font-weight:700;line-height:1;white-space:nowrap}
  .brand__square{flex:none;background:currentColor}
  .brand--cover{left:150px;top:80px;font-size:11px}
  .brand--cover .brand__square{width:7px;height:7px}
  .brand--corner{right:22px;top:11px;color:var(--headline);font-size:5px}
  .brand--corner .brand__square{width:4px;height:4px}
  .brand--end{left:182px;top:24px;font-size:8.5px}
  .brand--end .brand__square{width:6px;height:6px}
  .url{position:absolute;color:var(--white);font-size:4.4px;font-weight:700}
  .blob{position:absolute;right:0;bottom:0}
  .headline{position:absolute;color:var(--headline);font-weight:700;font-size:10.5px;line-height:1.28}
  .rule{display:block;width:26px;height:1.6px;background:var(--band);margin-top:7px}
  .copy{position:absolute;color:var(--body);font-size:3.3px;line-height:1.9}
  .copy p+p{margin-top:3px}
  .copy--light{color:var(--white)}
  .source{position:absolute;left:0;right:0;bottom:0;height:11px;background:var(--band);color:var(--white);font-size:3.3px;padding:3.6px 0 0 22px}
  .pagenum{position:absolute;right:15px;bottom:0;width:24px;height:14px;border-radius:12px 12px 0 0;background:var(--accent);color:var(--white);font-size:6.5px;font-weight:700;text-align:center;padding-top:3.5px}
  .photo{position:absolute;background:linear-gradient(135deg,var(--photo-b),var(--photo-a))}
  .media-band{position:absolute;left:0;right:0;top:81px;bottom:0;background:var(--band-soft)}
  .frame{position:absolute;left:16px;top:29px;width:170px;height:122px;background:var(--white);box-shadow:0 1px 4px rgba(0,0,0,.25);padding:5px}
  .frame .photo{position:static;width:100%;height:100%;background:linear-gradient(135deg,#eceff2,#b9bdc3)}
  .play{position:absolute;left:73px;top:49px}
  .highlight{position:absolute;left:161px;width:135px;height:34px;border-radius:5px;background:var(--band);border-left:3px solid var(--accent);padding:5px 10px;color:var(--white)}
  .highlight h3{font-size:4.2px;font-weight:700;margin-bottom:2px}
  .highlight p{font-size:3.1px;line-height:1.8}
  .thanks{position:absolute;left:185px;top:78px;color:var(--white);font-weight:400;font-size:23px;line-height:1.15;letter-spacing:.02em}
</style>
</head>
<body>
<main class="deck">

  <section class="slide slide--dark">
    <div class="backdrop" role="img" aria-label="Tinted photo of a clinic building facade with arching light-blue decorative sweeps"></div>
    <div class="brand brand--cover"><span class="brand__square"></span><span>Lindholm &amp; Vessner</span></div>
    <span class="url" style="left:187px;top:162px">www.strahlenkurse-beispiel.de</span>
    <svg class="blob" width="32" height="26" viewBox="0 0 32 26"><path d="M0 26 C0 10 10 0 24 0 L32 0 L32 26 Z" fill="#5b86c9"/></svg>
  </section>

  <section class="slide">
    <div class="brand brand--corner"><span class="brand__square"></span><span>Lindholm &amp; Vessner</span></div>
    <h2 class="headline" style="left:22px;top:22px">Your Headline<br>Goes Here<span class="rule"></span></h2>
    <div class="copy" style="left:22px;top:66px;width:272px">
      <p>Lorem ipsum dolor sit amet, consectetur adipiscing elit, sed do eiusmod tempor incididunt ut labore et dolore magna aliqua. Ut enim ad minim veniam, quis nostrud exercitation ullamco laboris nisi ut aliquip ex ea commodo consequat. Duis aute irure dolor in reprehenderit in voluptate velit esse cillum dolore eu fugiat nulla pariatur. Excepteur sint occaecat cupidatat non proident, sunt in culpa qui officia deserunt mollit anim id est laborum. Lorem ipsum dolor sit amet, consectetur adipiscing elit, sed do eiusmod tempor incididunt ut labore et dolore magna aliqua.</p>
      <p>Lorem ipsum dolor sit amet, consectetur adipiscing elit, sed do eiusmod tempor incididunt ut labore et dolore magna aliqua. Ut enim ad minim veniam, quis nostrud exercitation ullamco laboris nisi ut aliquip ex ea commodo consequat. Duis aute irure dolor in reprehenderit in voluptate velit esse cillum dolore eu fugiat nulla pariatur. Excepteur sint occaecat cupidatat non proident, sunt in culpa qui officia deserunt mollit anim id est laborum.</p>
    </div>
    <div class="source">Lorem ipsum dolor sit amet, consectetur adipiscing elit, sed do eiusmod tempor incididunt ut labore et dolore magna aliqua.</div>
    <div class="pagenum">01</div>
  </section>

  <section class="slide">
    <div class="brand brand--corner"><span class="brand__square"></span><span>Lindholm &amp; Vessner</span></div>
    <h2 class="headline" style="left:22px;top:22px">Your Headline<br>Goes Here<span class="rule"></span></h2>
    <div class="copy" style="left:22px;top:66px;width:125px">
      <p>Lorem ipsum dolor sit amet, consectetur adipiscing elit, sed do eiusmod tempor incididunt ut labore et dolore magna aliqua. Ut enim ad minim veniam, quis nostrud exercitation ullamco laboris nisi ut aliquip ex ea commodo consequat. Duis aute irure dolor in reprehenderit in voluptate velit esse cillum dolore eu fugiat nulla pariatur. Excepteur sint occaecat cupidatat non proident, sunt in culpa qui officia deserunt mollit anim id est laborum. Lorem ipsum dolor sit amet, consectetur adipiscing elit, sed do eiusmod tempor incididunt ut labore et dolore magna aliqua. Ut enim ad minim veniam, quis nostrud exercitation.</p>
    </div>
    <div class="photo" role="img" aria-label="Greyscale photo of an X-ray C-arm in a treatment room" style="left:170px;top:29px;width:130px;height:123px;border-radius:6px"></div>
    <div class="source">Lorem ipsum dolor sit amet, consectetur adipiscing elit, sed do eiusmod tempor incididunt ut labore et dolore magna aliqua.</div>
    <div class="pagenum">02</div>
  </section>

  <section class="slide">
    <div class="media-band"></div>
    <div class="brand brand--corner"><span class="brand__square"></span><span>Lindholm &amp; Vessner</span></div>
    <div class="frame"><div class="photo" role="img" aria-label="Greyscale photo of a monitor showing CT scans above a keyboard"></div></div>
    <svg class="play" width="24" height="24" viewBox="0 0 24 24"><circle cx="12" cy="12" r="10.5" fill="rgba(255,255,255,.45)" stroke="#fff" stroke-width="1.2"/><path d="M9.5 7.5 L17 12 L9.5 16.5 Z" fill="#fff"/></svg>
    <h2 class="headline" style="left:201px;top:33px">Your Headline<br>Goes Here<span class="rule"></span></h2>
    <div class="copy copy--light" style="left:201px;top:90px;width:100px">
      <p>Lorem ipsum dolor sit amet, consectetur adipiscing elit, sed do eiusmod tempor incididunt ut labore et dolore magna aliqua. Ut enim ad minim veniam, quis nostrud exercitation ullamco laboris nisi ut aliquip ex ea commodo consequat. Duis aute irure dolor in reprehenderit in voluptate velit esse cillum dolore eu fugiat nulla pariatur. Excepteur sint occaecat cupidatat non proident, sunt in culpa qui officia deserunt mollit anim id est laborum. Lorem ipsum dolor sit amet.</p>
    </div>
    <div class="source">Lorem ipsum dolor sit amet, consectetur adipiscing elit, sed do eiusmod tempor incididunt ut labore et dolore magna aliqua.</div>
    <div class="pagenum">03</div>
  </section>

  <section class="slide">
    <div class="brand brand--corner"><span class="brand__square"></span><span>Lindholm &amp; Vessner</span></div>
    <h2 class="headline" style="left:22px;top:22px">Your Headline<br>Goes Here<span class="rule"></span></h2>
    <div class="copy" style="left:22px;top:66px;width:118px">
      <p>Lorem ipsum dolor sit amet, consectetur adipiscing elit, sed do eiusmod tempor incididunt ut labore et dolore magna aliqua. Ut enim ad minim veniam, quis nostrud exercitation ullamco laboris nisi ut aliquip ex ea commodo consequat. Duis aute irure dolor in reprehenderit in voluptate velit esse cillum dolore eu fugiat nulla pariatur. Excepteur sint occaecat cupidatat non proident, sunt in culpa qui officia deserunt mollit anim id est laborum. Lorem ipsum dolor sit amet, consectetur adipiscing elit, sed do eiusmod tempor incididunt ut labore et dolore magna aliqua. Ut enim ad minim veniam, quis nostrud exercitation.</p>
    </div>
    <div class="highlight" style="top:33px"><h3>Lorem ipsum dolor</h3><p>Lorem ipsum dolor sit amet, consectetur adipiscing elit, sed do eiusmod tempor incididunt ut labore et dolore magna aliqua. Ut enim ad minim veniam, quis nostrud exercitation ullamco laboris nisi.</p></div>
    <div class="highlight" style="top:73px"><h3>Lorem ipsum dolor</h3><p>Lorem ipsum dolor sit amet, consectetur adipiscing elit, sed do eiusmod tempor incididunt ut labore et dolore magna aliqua. Ut enim ad minim veniam, quis nostrud exercitation ullamco laboris nisi.</p></div>
    <div class="highlight" style="top:113px"><h3>Lorem ipsum dolor</h3><p>Lorem ipsum dolor sit amet, consectetur adipiscing elit, sed do eiusmod tempor incididunt ut labore et dolore magna aliqua. Ut enim ad minim veniam, quis nostrud exercitation ullamco laboris nisi.</p></div>
    <div class="source">Lorem ipsum dolor sit amet, consectetur adipiscing elit, sed do eiusmod tempor incididunt ut labore et dolore magna aliqua.</div>
    <div class="pagenum">04</div>
  </section>

  <section class="slide slide--dark">
    <div class="backdrop" role="img" aria-label="Tinted photo of a clinic building facade with arching light-blue decorative sweeps"></div>
    <div class="brand brand--end"><span class="brand__square"></span><span>Lindholm &amp; Vessner</span></div>
    <h2 class="thanks">VIELEN<br>DANKE</h2>
    <span class="url" style="left:184px;top:162px">www.strahlenkurse-beispiel.de</span>
    <svg class="blob" width="32" height="26" viewBox="0 0 32 26"><path d="M0 26 C0 10 10 0 24 0 L32 0 L32 26 Z" fill="#5b86c9"/></svg>
  </section>

</main>
</body>
</html>
```